Wordpress Design Project

I have a main site www.tinymolarclinic.example for 9 dental offices. I want a designed wordpress mini-site template that I can use to create mini sites for each location and related projects that keeps the look and feel of the home site.
Updates

I'm getting different designs from my original web site. Maybe I'm confusing the designers but to clarify:

what I want is to keep the same graphics as we already have on this site www.tinymolarclinic.example and just convert it to a Wordpress site template to be used as individual MINI sites. 

No new designs needed, same design just different platform.

Target Market(s)

see site www.tinymolarclinic.example

Industry/Entity Type

Dental

Requirements
Must have
• Can we make the Logo larger?
Should not have
• I think you're basing your designs on tinymolarclinicglendale.example but I specifically said it should be based on the home site which is www.tinymolarclinic.example
Please view the difference. I need for it to have the same APPEARANCE. Please!
http://www.tinymolarclinic.example/

```html
<!DOCTYPE html>
<html lang="en">
<head>
<meta charset="utf-8">
<title>Tiny Molar Clinic</title>
<link href="https://fonts.googleapis.com/css2?family=Source+Sans+3:wght@400;600&display=swap" rel="stylesheet">
<style>
:root{
  --bg-inner:#ffe27a;
  --bg-outer:#fbbf3f;
  --panel:#ffffff;
  --ink:#2a2a2a;
  --muted:#3a3a3a;
  --red:#d42a1f;
  --teal:#14a898;
  --orange:#f3731a;
  --dot:#a9dcf6;
}
*{box-sizing:border-box;margin:0;padding:0}
html,body{width:1096px;height:1200px;overflow:hidden}
body{
  font-family:"Source Sans 3",sans-serif;color:var(--ink);
  background:radial-gradient(ellipse at 50% 40%,var(--bg-inner) 0%,#ffd35c 45%,var(--bg-outer) 100%);
  position:relative;
}
.page{position:absolute;left:126px;top:0;width:843px;height:1113px;background:var(--panel)}
.page-shadow{position:absolute;left:170px;top:1110px;width:760px;height:12px;border-radius:50%;
  background:radial-gradient(ellipse at center,rgba(90,60,0,.45),rgba(90,60,0,0) 70%)}
.abs{position:absolute}

.brand{left:20px;top:12px;display:flex;align-items:center;gap:12px}
.brand-mark{width:104px;height:104px;border-radius:50%;background:#f2c23a;flex:none}
.brand-name{font-size:25px;font-weight:600;color:var(--red);line-height:1.05;width:110px}

.tollfree{left:342px;top:32px;font-size:17px;color:var(--ink)}
.lang{left:470px;top:87px;width:160px;height:24px;border-radius:4px;background:var(--teal);
  color:#fff;font-size:11px;padding:4px 9px;display:flex;justify-content:space-between;align-items:center}
.lang svg{width:9px;height:6px}
.mascot{left:670px;top:4px;width:150px;height:130px;border-radius:40% 40% 30% 30%;
  background:radial-gradient(circle at 55% 40%,#c98a5a,#a2663e 60%,rgba(255,255,255,0) 72%)}

.nav{left:22px;top:135px;display:flex;gap:3px}
.nav a{height:26px;border-radius:13px;color:#fff;font-size:13px;text-decoration:none;
  display:flex;align-items:center;justify-content:center;box-shadow:inset 0 -3px 4px rgba(0,0,0,.12)}
.n-home{width:67px;background:#9a35e6}
.n-appt{width:100px;background:#35c2ef}
.n-promise{width:65px;background:#ef6a13}
.n-gallery{width:54px;background:#f2a20c}
.n-services{width:63px;background:#97cf2c}
.n-about{width:67px;background:#a7e6f7}
.n-contact{width:68px;background:#1d4f9b}
.n-faq{width:53px;background:#e0161a}
.n-patient{width:100px;background:#1432c8}
.n-locations{width:72px;background:#f0632f}
.n-blog{width:54px;background:#7fd7d2}

.hero-photo{left:34px;top:184px;width:461px;height:284px;border-radius:40% 40% 0 0/30% 30% 0 0;
  background:linear-gradient(180deg,#d9b08c 0%,#c68f66 45%,#ece7e0 100%)}
.hero-shadow{left:42px;top:464px;width:754px;height:8px;border-radius:50%;
  background:radial-gradient(ellipse at center,rgba(0,0,0,.35),rgba(0,0,0,0) 70%)}
.hero-title{left:507px;top:238px;font-size:17px;font-weight:400;color:var(--ink)}
.hero-text{left:512px;top:270px;width:269px;font-size:11.5px;line-height:17px;text-align:justify;color:var(--muted)}
.learn{left:594px;top:388px;width:124px;height:27px;border-radius:13px;background:linear-gradient(#f78b32,var(--orange));
  color:#fff;font-size:15px;display:flex;align-items:center;justify-content:center;box-shadow:0 2px 3px rgba(0,0,0,.25)}
.dots{left:668px;top:440px;display:flex;gap:7px}
.dots span{width:12px;height:12px;border-radius:50%;background:var(--dot)}

.h-red{color:var(--red);font-size:15.5px;font-weight:400}
.welcome-title{left:27px;top:504px}
.welcome-text{left:27px;top:535px;width:535px;font-size:11.2px;line-height:17px;color:var(--muted)}
.kids-photo{left:584px;top:494px;width:208px;height:139px;border-radius:45% 45% 8px 8px;
  background:linear-gradient(160deg,#e9b48c 0%,#3a6fb7 70%,#d93a2c 100%)}
.serve-title{left:27px;top:619px}
.serve-text{left:27px;top:649px;width:780px;font-size:12.5px;line-height:20px;color:var(--muted)}

.office{position:absolute;width:244px;height:112px;border-radius:4px;padding:8px 15px;
  box-shadow:0 6px 6px -4px rgba(0,0,0,.35)}
.office h3{font-size:17px;font-weight:400;color:#1f1f1f;margin-bottom:6px}
.office p{font-size:12px;line-height:20px;padding-left:22px;color:#1f1f1f}
.c1{left:29px}.c2{left:299px}.c3{left:569px}
.r1{top:707px}.r2{top:835px}.r3{top:962px}
.sky{background:linear-gradient(#a9dcfb,#62b1f3)}
.lime{background:linear-gradient(#b9e42c,#a3d51d)}
.pink{background:linear-gradient(#ff8fcb,#ff52a6)}
.tangerine{background:linear-gradient(#ffa23c,#ff700c)}
.violet{background:linear-gradient(#e36fe9,#a54bb8)}
.ice{background:linear-gradient(#e3f3fb,#bfdcf5)}
.steel{background:linear-gradient(#52b1e0,#2c91c4)}
.aqua{background:linear-gradient(#9be4f8,#10b3e4)}
.leaf{background:linear-gradient(#d4ec8b,#9cc84a)}

.copyright{left:142px;top:1138px;font-size:12px;color:var(--ink)}
.follow{left:784px;top:1134px;display:flex;align-items:center;gap:9px;font-size:12px}
.follow span.icon{width:28px;height:28px;border-radius:4px;box-shadow:0 2px 2px rgba(0,0,0,.25)}
.i1{background:#5ec4ee}.i2{background:#3d67b2}.i3{background:#2f7fa6}
</style>
</head>
<body>
<div class="page-shadow"></div>
<main class="page">
  <div class="abs brand"><span class="brand-mark"></span><span class="brand-name">Tiny Molar Clinic</span></div>
  <div class="abs tollfree">Call us Toll Free : 1-888-TINY-MOL (555-0142)</div>
  <div class="abs lang">Select your Language <svg viewBox="0 0 9 6"><path d="M0 0h9L4.5 6z" fill="#fff"/></svg></div>
  <div class="abs mascot" role="img" aria-label="Cartoon beaver mascot holding a toothbrush and toothpaste"></div>

  <nav class="abs nav">
    <a class="n-home" href="#">Home</a><a class="n-appt" href="#">Appointment</a><a class="n-promise" href="#">Promise</a>
    <a class="n-gallery" href="#">Gallery</a><a class="n-services" href="#">Services</a><a class="n-about" href="#">About Us</a>
    <a class="n-contact" href="#">Contact</a><a class="n-faq" href="#">FAQ's</a><a class="n-patient" href="#">Patient Log In</a>
    <a class="n-locations" href="#">Locations</a><a class="n-blog" href="#">Blog</a>
  </nav>

  <div class="abs hero-photo" role="img" aria-label="Photo of five smiling children giving thumbs up"></div>
  <div class="abs hero-shadow"></div>
  <h2 class="abs hero-title">Every one smile in the same language</h2>
  <p class="abs hero-text">Sed ut perspiciatis unde omnis iste natus error sit voluptatem accusantium doloremque laudantium, totam rem aperiam, eaque ipsa quae ab illo inventore veritatis et quasi architecto beatae vitae dicta sunt explicabo. Nemo enim ipsam voluptatem quia voluptas sit aspernatur aut odit aut fugit, sed quia consequuntur</p>
  <div class="abs learn">LEARN MORE</div>
  <div class="abs dots"><span></span><span></span><span></span><span></span></div>

  <h2 class="abs h-red welcome-title">WELCOME TO OUR WEBSITE</h2>
  <p class="abs welcome-text">Sed ut perspiciatis unde omnis iste natus error sit voluptatem accusantium doloremque laudantium, totam rem aperiam, eaque ipsa quae ab illo inventore veritatis et quasi architecto beatae vitae dicta sunt explicabo. Nemo enim ipsam voluptatem quia voluptas sit aspernatur aut odit aut fugit, sed quia consequuntur</p>
  <div class="abs kids-photo" role="img" aria-label="Photo of two young boys brushing their teeth"></div>

  <h2 class="abs h-red serve-title">LOOK AND CLICK BELOW FOR THE OFFICE TO SERVE YOU.</h2>
  <p class="abs serve-text">Tiny Molar Clinic accepts all private insurances, SmileAid &amp; all major credit cards, Financial assistance may be arranged for those with financial need. At Tiny Molar Clinic, we are your servants providing the highest quality dental care to you and your loved ones.</p>

  <div class="office c1 r1 sky"><h3>Hollywood</h3><p>4905 Cedar Grove Blvd<br>Los Angeles, CA 90027<br>(323) 555-0118</p></div>
  <div class="office c2 r1 lime"><h3>East LA</h3><p>4900 Lantern Hill Blvd<br>Los Angeles, CA 90022<br>(323) 555-0176</p></div>
  <div class="office c3 r1 pink"><h3>El Monte</h3><p>11017 E. Maple Ridge Blvd<br>El Monte, CA 91731<br>(626) 555-0193</p></div>
  <div class="office c1 r2 tangerine"><h3>Hollywood</h3><p>4905 Cedar Grove Blvd<br>Los Angeles, CA 90027<br>(323) 555-0118</p></div>
  <div class="office c2 r2 violet"><h3>East LA</h3><p>4900 Lantern Hill Blvd<br>Los Angeles, CA 90022<br>(323) 555-0176</p></div>
  <div class="office c3 r2 ice"><h3>El Monte</h3><p>11017 E. Maple Ridge Blvd<br>El Monte, CA 91731<br>(626) 555-0193</p></div>
  <div class="office c1 r3 steel"><h3>Hollywood</h3><p>4905 Cedar Grove Blvd<br>Los Angeles, CA 90027<br>(323) 555-0118</p></div>
  <div class="office c2 r3 aqua"><h3>East LA</h3><p>4900 Lantern Hill Blvd<br>Los Angeles, CA 90022<br>(323) 555-0176</p></div>
  <div class="office c3 r3 leaf"><h3>El Monte</h3><p>11017 E. Maple Ridge Blvd<br>El Monte, CA 91731<br>(626) 555-0193</p></div>
</main>

<footer>
  <div class="abs copyright">© 2012.www.tinymolarclinic.example</div>
  <div class="abs follow">Follow us: <span class="icon i1"></span><span class="icon i2"></span><span class="icon i3"></span></div>
</footer>
</body>
</html>
```